Brand Identity Stationary Package

Hello I'm looking for a full branding package for my Property Management Company. I have a logo but looking to have the following
Business Card
Email signature
Facebook cover photo
Letterhead (word.doc)
#10 Envelope
Pocket Folder - link to 9x12 pocket folder design specs https://www.printorbit-example.ca/marketing-materials/presentation-folders
would like everything to match and be brand identifiable. The company looks after residential properties/apartments and some commercial properties. Attached is a zip of the files.
For Business Card
Name: Gareth Lindqvist
Position: Operations Manager
Number: 1 (555) 384-2917
Email: Gareth@harborkey-example.ca
Website: Harborkey-example.ca
Property Management

```html
<!DOCTYPE html>
<html lang="en">
<head>
<meta charset="utf-8">
<title>Harborkey Pocket Folder</title>
<link rel="stylesheet" href="https://fonts.googleapis.com/css2?family=Montserrat:wght@400;600;700&family=Open+Sans:wght@400;600&display=swap">
<style>
:root{
  --green:#84ad3c;
  --green-dark:#6b8f34;
  --ink:#151515;
  --paper:#ffffff;
  --paper-shade:#e6e6e6;
  --backdrop:#b9b8b9;
  --muted:#555;
}
*{box-sizing:border-box;margin:0;padding:0}
html,body{width:982px;height:1200px;overflow:hidden}
body{background:var(--backdrop);font-family:"Montserrat",sans-serif;position:relative}
.spread{position:absolute;left:91px;width:800px;height:533px;display:flex;box-shadow:0 12px 30px rgba(0,0,0,.25)}
.spread--outside{top:40px}
.spread--inside{top:627px}
.panel{position:relative;width:400px;height:533px;overflow:hidden}

/* back cover */
.back-cover{background:linear-gradient(90deg,var(--green),var(--green-dark))}
.brand-name{font-family:"Montserrat",sans-serif;font-weight:700;letter-spacing:2px;color:var(--ink)}
.back-cover .brand-name{position:absolute;top:48px;left:0;width:100%;text-align:center;font-size:26px}
.back-cover__tagline{position:absolute;top:410px;width:100%;text-align:center;color:#fff;font-size:9px;font-weight:700;line-height:15px;letter-spacing:.3px}
.back-cover__rule{position:absolute;top:448px;left:40px;width:320px;height:1px;background:rgba(255,255,255,.7)}
.back-cover__contact{position:absolute;top:458px;width:100%;display:flex;justify-content:center;gap:10px;color:#fff;font-family:"Open Sans",sans-serif;font-size:10.5px}
.back-cover__contact span{display:flex;align-items:center;gap:3px}
.icon{width:9px;height:9px;fill:currentColor}

/* front cover */
.front-cover{background:linear-gradient(180deg,var(--paper),var(--paper-shade))}
.front-cover .brand-name{position:absolute;top:58px;width:100%;text-align:center;font-size:40px;letter-spacing:3px}
.front-cover__subline{position:absolute;top:112px;width:100%;text-align:center;font-size:9px;font-weight:600;letter-spacing:6px;color:var(--ink)}
.front-cover__watermark{position:absolute;top:230px;width:100%;text-align:center;font-size:44px;font-weight:700;color:#d6d6d6;letter-spacing:3px}
.front-cover__wave{position:absolute;left:0;bottom:0;width:400px;height:533px}

/* inside */
.inside-left{background:linear-gradient(90deg,var(--paper) 10%,#c9c9c9)}
.inside-right{background:linear-gradient(90deg,#bdbdbd,var(--paper) 25%)}
.pocket{position:absolute;left:0;top:0;width:400px;height:533px}

.letterhead{position:absolute;top:22px;left:36px;width:340px;height:470px;background:var(--paper);box-shadow:-4px 4px 10px rgba(0,0,0,.2);padding:18px 20px}
.letterhead__top{display:flex;justify-content:space-between;align-items:flex-end}
.letterhead .brand-name{font-size:17px}
.letterhead__contact{font-size:6.5px;line-height:9px;color:var(--ink)}
.letterhead__name{color:var(--green);font-weight:700}
.letterhead__rule{height:1.5px;background:var(--green);margin:10px 0 22px}
.letterhead__body{font-size:6.3px;line-height:8.4px;color:#333}
.letterhead__body p{margin-bottom:8px}
</style>
</head>
<body>

<section class="spread spread--outside">
  <div class="panel back-cover">
    <div class="brand-name">HARBORKEY</div>
    <div class="back-cover__tagline">TENANTS, AND LANDLORDS<br>PROPERTY MANAGEMENT</div>
    <div class="back-cover__rule"></div>
    <div class="back-cover__contact">
      <span><svg class="icon" viewBox="0 0 10 10"><path d="M2 1l2 2-1 1.5c.8 1.3 1.3 1.8 2.5 2.5L7 6l2 2-1.5 1.5C4 9 1 6 .5 2.5z"/></svg>1 (555) 384-2917</span>
      <span><svg class="icon" viewBox="0 0 10 10"><path d="M0 2h10v6H0z M0 2l5 3.5L10 2" stroke="#6b8f34" stroke-width=".8"/></svg>Gareth@harborkey-example.ca</span>
      <span><svg class="icon" viewBox="0 0 10 10"><circle cx="5" cy="5" r="4.5"/></svg>Harborkey-example.ca</span>
    </div>
  </div>

  <div class="panel front-cover">
    <div class="brand-name">HARBORKEY</div>
    <div class="front-cover__subline">PROPERTY MANAGEMENT</div>
    <div class="front-cover__watermark">HARBORKEY</div>
    <svg class="front-cover__wave" viewBox="0 0 400 533" aria-hidden="true">
      <path d="M40,440 C120,500 220,470 300,448 S380,430 395,432" fill="none" stroke="#151515" stroke-width="3"/>
      <path d="M0,395 C40,450 130,480 220,462 S360,425 400,438 L400,533 L0,533 Z" fill="#84ad3c"/>
    </svg>
  </div>
</section>

<section class="spread spread--inside">
  <div class="panel inside-left">
    <svg class="pocket" viewBox="0 0 400 533" aria-hidden="true">
      <path d="M0,360 L330,330 Q345,329 352,340 L400,533 L0,533 Z" fill="#84ad3c"/>
    </svg>
  </div>

  <div class="panel inside-right">
    <article class="letterhead">
      <div class="letterhead__top">
        <div class="brand-name">HARBORKEY</div>
        <div class="letterhead__contact">
          <div class="letterhead__name">GARETH LINDQVIST</div>
          <div>Operations Manager</div>
          <div>1 (555) 384-2917</div>
          <div>Gareth@harborkey-example.ca</div>
          <div>Harborkey-example.ca</div>
        </div>
      </div>
      <div class="letterhead__rule"></div>
      <div class="letterhead__body">
        <p>Mr/s<br>First Name and Last Name<br>Company Name<br>Address</p>
        <p>Lorem ipsum dolor sit amet, consectetur adipiscing sed do eiusmod tempor incididunt labore et dolore magna aliqua. Ut enim ad minim veniam, quis nostrud exercitation ullamco laboris nisi ut aliquip exea commodo consequat.</p>
        <p>Lorem ipsum dolor sit amet, consectetur adipiscing sed do eiusmod tempor incididunt labore et dolore magna aliqua. Ut enim ad minim veniam, quis nostrud exercitation ullamco laboris nisi ut aliquip exea commodo consequat. Duis aute irure dolor in reprehenderit in voluptate velit esse irure.</p>
        <p>Lorem ipsum dolor sit amet, consectetur adipiscing sed do eiusmod tempor incididunt labore et dolore magna aliqua. Consequat. Duis aute irure dolor in reprehenderit in voluptate velit esse cillum dolore eu fugiat nulla pariatur.</p>
        <p>Lorem ipsum dolor sit amet, consectetur adipiscing sed do eiusmod tempor incididunt labore et dolore magna aliqua. Ut enim Lorem ipsum dolor sit amet, consectetur adipiscing sed do eiusmod.</p>
        <p>Lorem ipsum dolor sit amet, consectetur adipiscing sed do eiusmod tempor incididunt labore et dolore magna aliqua. Ut enim ad minim veniam, quis nostrud exercitation ullamco laboris nisi ut aliquip.</p>
        <p>Regards,</p>
      </div>
    </article>
    <svg class="pocket" viewBox="0 0 400 533" aria-hidden="true">
      <path d="M12,533 L38,345 Q42,327 62,325 L400,292 L400,533 Z" fill="#84ad3c"/>
    </svg>
  </div>
</section>

</body>
</html>
```